Professional Services - letterhead / business cards

The company (velmora partners) will provide services to Investment Funds and large investors in Spain. I have recently chosen a logo that I am attaching.

I would like a simple stationary design that i could use as letter head, business cards and "with compliments" cards.

I am not quite sure which color I will mostly use for the logo, in the email signature I will probably lean towards the white background and grey letters. I am attaching my favourite options.

Target Market(s)

Large Multinationals, Investment funds and Law firms

Industry/Entity Type

Business

Requirements
Must have
• my details are:
Luis R. Abadal
Velmora Partners S.L.
Casa de Torrelumbre
Calle de Vientoalto 27
28014 Madrid
T: +34 (91) 387-2265
M: +34 (646) 819-054
e-mail: labadal@velmorapartners.com

```html
<!DOCTYPE html>
<html lang="en">
<head>
<meta charset="utf-8">
<title>Velmora Partners – Stationery</title>
<link href="https://fonts.googleapis.com/css2?family=Didact+Gothic&family=PT+Sans:wght@400;700&family=Playball&display=swap" rel="stylesheet">
<style>
:root{
  --navy:#26246b;
  --grey:#a8a9ad;
  --text-grey:#7b7b80;
  --paper:#ffffff;
  --paper-shade:#ececee;
  --backdrop:#b9774c;
  --logo-font:"Didact Gothic", sans-serif;
  --body-font:"PT Sans", sans-serif;
  --script-font:"Playball", cursive;
}
*{box-sizing:border-box;margin:0;padding:0}
html,body{width:1200px;height:454px;overflow:hidden}
body{background:var(--backdrop);position:relative;font-family:var(--body-font)}
.sheet{position:absolute;background:var(--paper);overflow:hidden;box-shadow:0 1px 3px rgba(0,0,0,.25)}
.wave{position:absolute;left:0;bottom:0;width:100%;display:block}
.brand{font-family:var(--logo-font);color:var(--navy);white-space:nowrap;position:absolute;letter-spacing:.2px}
.brand--light{color:var(--paper)}
.small{position:absolute;font-size:6px;line-height:1.45;color:var(--text-grey)}
.contact{position:absolute;right:6px;text-align:right;color:var(--paper);line-height:1.7}
.contact span::before{content:"";display:inline-block;width:4px;height:4px;border:1px solid var(--paper);border-radius:50%;margin-right:3px;vertical-align:middle}

/* letterhead */
.letterhead{left:10px;top:9px;width:335px;height:433px;background:linear-gradient(160deg,#fff 30%,#f1f1f3)}
.letterhead .brand{left:16px;top:16px;font-size:20px}
.letterhead .address{left:246px;top:17px;padding-left:5px;border-left:1px solid #ccc}
.letterhead .contact{bottom:10px;right:18px;font-size:6.5px}

/* envelopes */
.envelope-back{left:460px;top:10px;width:372px;height:239px;background:linear-gradient(#f6f6f7,#e6e6e8)}
.envelope-back .flap{position:absolute;left:0;top:0;width:100%;height:70px}
.envelope-back .brand{left:0;right:0;text-align:center;top:22px;font-size:20px}
.envelope-open{left:378px;top:83px;width:374px;height:166px;background:#f7f7f8}
.envelope-open .flap{position:absolute;left:0;top:0;width:100%;height:96px}
.envelope-open .brand{left:0;right:0;text-align:center;top:24px;font-size:22px}
.envelope-front{left:417px;top:157px;width:374px;height:167px;background:linear-gradient(170deg,#fff 20%,#e9e9eb)}
.envelope-front .brand{left:10px;top:12px;font-size:20px}
.envelope-front .address{left:10px;top:44px;font-size:5.5px}

/* compliments slip */
.compliments{left:866px;top:157px;width:326px;height:154px}
.compliments .brand{left:18px;top:20px;font-size:22px}
.compliments .script{position:absolute;left:19px;top:106px;font-family:var(--script-font);font-size:15px;color:var(--navy)}
.compliments .address{left:19px;top:116px;margin-top:16px;font-size:6px;color:#555}
.compliments .contact{bottom:8px;font-size:6px}
.label{position:absolute;left:964px;top:320px;font-family:var(--body-font);font-size:18px;color:var(--paper)}

/* business cards */
.card{top:351px;width:169px;height:95px}
.card--details{left:383px}
.card--details .brand{left:10px;top:15px;font-size:11.5px}
.card--details .name{position:absolute;left:11px;top:38px;font-size:6.5px;font-weight:700;color:var(--navy)}
.card--details .name em{font-style:normal;font-weight:400;font-size:4px;color:var(--text-grey)}
.card--details .address{left:11px;top:51px;font-size:4px}
.card--details .contact{bottom:3px;right:4px;font-size:4px}
.card--plain{left:559px}
.card--navy{left:735px;background:var(--navy)}
.card--plain .brand,.card--navy .brand{left:0;right:0;text-align:center;top:40px;font-size:15px}
</style>
</head>
<body>

<!-- Letterhead -->
<section class="sheet letterhead" aria-label="Letterhead">
  <div class="brand">velmora partners</div>
  <div class="small address">Casa de Torrelumbre<br>Calle de Vientoalto 27<br>28014 Madrid</div>
  <svg class="wave" viewBox="0 0 400 60" height="48" preserveAspectRatio="none" aria-hidden="true">
    <path d="M0,40 C130,44 260,26 400,6" fill="none" stroke="var(--grey)" stroke-width="7"/>
    <path d="M0,60 L0,50 C130,52 260,32 400,14 L400,60Z" fill="var(--navy)"/>
  </svg>
  <div class="contact"><span>+34 (91) 387-2265</span></div>
</section>

<!-- Envelope, back with dark flap -->
<section class="sheet envelope-back" aria-label="Envelope back">
  <svg class="flap" viewBox="0 0 372 70" preserveAspectRatio="none" aria-hidden="true">
    <path d="M0,0 H372 L372,12 C360,30 300,40 215,62 C195,70 177,70 157,62 C72,40 12,30 0,12Z" fill="var(--navy)"/>
  </svg>
  <div class="brand brand--light">velmora</div>
</section>

<!-- Envelope, open flap -->
<section class="sheet envelope-open" aria-label="Envelope with open flap">
  <svg class="flap" viewBox="0 0 374 96" preserveAspectRatio="none" aria-hidden="true">
    <path d="M2,1 H372 L372,14 C360,40 300,60 215,86 C195,95 179,95 159,86 C74,60 14,40 2,14Z" fill="#fff" stroke="#333" stroke-width="1"/>
  </svg>
  <div class="brand">velmora</div>
</section>

<!-- Envelope front -->
<section class="sheet envelope-front" aria-label="Envelope front">
  <div class="brand">velmora partners</div>
  <div class="small address">Casa de Torrelumbre, Calle de Vientoalto 27, 28014 Madrid</div>
  <svg class="wave" viewBox="0 0 400 60" height="40" preserveAspectRatio="none" aria-hidden="true">
    <path d="M0,38 C130,40 260,24 400,6" fill="none" stroke="var(--grey)" stroke-width="7"/>
    <path d="M0,60 L0,47 C130,48 260,30 400,14 L400,60Z" fill="var(--navy)"/>
  </svg>
</section>

<!-- With compliments slip -->
<section class="sheet compliments" aria-label="With compliments slip">
  <div class="brand">velmora partners</div>
  <div class="script">With Compliments</div>
  <div class="small address">Casa de Torrelumbre<br>Calle de Vientoalto 27, 28014 Madrid</div>
  <svg class="wave" viewBox="0 0 400 80" height="60" preserveAspectRatio="none" aria-hidden="true">
    <path d="M0,56 C140,58 270,30 400,4" fill="none" stroke="var(--grey)" stroke-width="8"/>
    <path d="M0,80 L0,66 C140,66 270,38 400,14 L400,80Z" fill="var(--navy)"/>
  </svg>
  <div class="contact">
    <span>+34 (91) 387-2265</span><br>
    <span>+34 (646) 819-054</span><br>
    <span>labadal@velmorapartners.com</span>
  </div>
</section>
<div class="label">Compliments</div>

<!-- Business card, details side -->
<section class="sheet card card--details" aria-label="Business card front">
  <div class="brand">velmora partners</div>
  <div class="name">Luis R. Abadal, <em>Velmora Partners S.L.</em></div>
  <div class="small address">Casa de Torrelumbre<br>Calle de Vientoalto 27, 28014 Madrid</div>
  <svg class="wave" viewBox="0 0 400 80" height="44" preserveAspectRatio="none" aria-hidden="true">
    <path d="M0,52 C140,50 270,26 400,4" fill="none" stroke="var(--grey)" stroke-width="9"/>
    <path d="M0,80 L0,64 C140,62 270,36 400,15 L400,80Z" fill="var(--navy)"/>
  </svg>
  <div class="contact">
    <span>+34 (91) 387-2265</span><br>
    <span>+34 (646) 819-054</span><br>
    <span>labadal@velmorapartners.com</span>
  </div>
</section>

<!-- Business card, white logo side -->
<section class="sheet card card--plain" aria-label="Business card back, white">
  <div class="brand">velmora partners</div>
</section>

<!-- Business card, navy logo side -->
<section class="sheet card card--navy" aria-label="Business card back, navy">
  <div class="brand brand--light">velmora partners</div>
</section>

</body>
</html>
```